Small environmental consultancy needs a simple but professional web design

We are a boutique environmental consultancyand contracting business located in Margaret River in the South West of Western Australia.

We have two arms
1) Consulting which offers environmental planning, management and assessment services primarily to local government and the development industry.
2) Contracting which implements on site plans and on ground works primarily involving revegetation, bush regeneration and environmental weed control.

We need a simple yet professional web design within the wordpress platform that commmunicates professionalism, experience and technical expertise without appearing too corporate.

Something like this structure appeals:
http://fernquill.net.au/environment-services/
or
http://www.tallowbrookenvironmental.com.au/index.php

(without the image gallery function)

Target Market(s)

Local Government Officers deciding on tenders;
Developers, Engineers, Town Planning consultants looking for environmental expertise

Industry/Entity Type

Business

Number of Pages Required

5+ page

Font styles to use
Sans Serif

Colors
33a6d7
9bcb3c

Requirements
Must have
• Pages required include:
• Home
• Environmental Planning and Management
• Revegetation and Regeneration Implementation (This page can mirror the Environmental Planning and Management page exactly in structure but with different text and images)
• About Us (I think that this page can be relatively simple and generic)
• Contact (I think that this page can be very simple and generic)
Nice to have
• An ability to start out basic and quicikly establish a website presence and then build in additional drop downs and pages over time.
Should not have
• It does not need a photo gallery page;
• It does not need a major amount of space dedicated to social media and blogs etc as this is not currently particularly active area for us

```html
<!DOCTYPE html>
<html lang="en">
<head>
<meta charset="utf-8">
<title>Contact – Marri Ecoservices</title>
<link href="https://fonts.googleapis.com/css2?family=Open+Sans:ital,wght@0,400;0,600;0,700;1,400&family=Raleway:wght@700&family=Teko:wght@400;500&display=swap" rel="stylesheet">
<style>
  :root {
    --blue: #33a6d7;
    --blue-dark: #2a8cc4;
    --green: #9bcb3c;
    --brown: #7a4a1e;
    --header-bg: #f1f1f1;
    --panel: #efefef;
    --footer-bg: #eaeaea;
    --text: #444444;
    --heading: #2b2b2b;
    --line: #d4d4d4;
    --required: #d0021b;
    --icon-bg: #e3e3e3;
    --icon: #8a8a8a;
  }
  * { box-sizing: border-box; margin: 0; padding: 0; }
  html, body { width: 1087px; height: 1200px; overflow: hidden; }
  body {
    position: relative;
    background: #ffffff;
    font-family: "Open Sans", Arial, sans-serif;
    color: var(--text);
    font-size: 13px;
  }

  /* Header */
  .site-header { position: absolute; left: 0; top: 0; width: 1087px; height: 159px; background: var(--header-bg); }
  .brand { position: absolute; left: 66px; top: 48px; display: flex; align-items: center; gap: 16px; }
  .brand-mark { width: 54px; height: 54px; border-radius: 50%; background: var(--green); }
  .brand-name { font-family: "Open Sans", sans-serif; font-weight: 600; font-size: 34px; color: var(--brown); letter-spacing: 0.2px; }
  .call-top { position: absolute; right: 64px; top: 34px; text-align: left; }
  .call-top .label { font-weight: 700; font-size: 16px; color: #111; line-height: 1.1; }
  .call-top .number { font-weight: 700; font-size: 26px; color: var(--blue); line-height: 1.1; }
  .search { position: absolute; left: 827px; top: 95px; width: 192px; height: 26px; background: #fff; display: flex; align-items: center; justify-content: space-between; padding: 0 8px; font-size: 13px; color: #666; }

  /* Navigation */
  .main-nav { position: absolute; left: 0; top: 159px; width: 1087px; height: 39px; background: var(--blue); border-bottom: 2px solid var(--blue-dark); }
  .main-nav ul { list-style: none; display: flex; position: absolute; left: 72px; top: 0; height: 100%; }
  .main-nav li { font-family: "Raleway", sans-serif; font-weight: 700; font-size: 12px; color: #fff; text-transform: uppercase; padding: 0 20px; line-height: 37px; }
  .main-nav li.is-active { background: var(--blue-dark); padding: 0 23px; }

  /* Banner */
  .banner { position: absolute; left: 0; top: 198px; width: 1087px; height: 115px;
    background: linear-gradient(180deg, #9fbfd9 0%, #c9d9e6 30%, #4f5a3e 52%, #6d6a55 70%, #1f5a7a 85%, #134a6a 100%); }

  /* Page title */
  .page-title { position: absolute; left: 66px; top: 354px; font-family: "Teko", sans-serif; font-weight: 500; font-size: 34px; line-height: 1; color: var(--green); text-transform: uppercase; }

  /* Form */
  .contact-form { position: absolute; left: 67px; top: 415px; width: 627px; height: 437px; background: var(--panel); }
  .field-label { position: absolute; font-size: 12.5px; line-height: 17px; color: #333; }
  .field-label .req { color: var(--required); }
  .field { position: absolute; background: #fff; border: 1px solid #d6d6d6; border-radius: 3px; }
  .require-note { position: absolute; left: 520px; top: 364px; font-size: 12px; font-style: italic; color: #777; }
  .require-note .req { color: var(--required); font-style: normal; }
  .submit { position: absolute; left: 24px; top: 375px; width: 194px; height: 36px; background: var(--green); border-radius: 3px; color: #fff; font-family: "Teko", sans-serif; font-weight: 500; font-size: 22px; display: flex; align-items: center; justify-content: center; padding-top: 3px; text-transform: uppercase; }

  /* Contact info */
  .contact-info { position: absolute; left: 718px; top: 412px; width: 320px; }
  .section-heading { font-family: "Teko", sans-serif; font-weight: 400; font-size: 20px; color: var(--heading); text-transform: uppercase; line-height: 1; }
  .info-item { position: absolute; left: 0; display: flex; gap: 12px; font-size: 12px; color: #555; line-height: 1.45; }
  .info-icon { width: 30px; height: 30px; border-radius: 50%; background: var(--icon-bg); display: flex; align-items: center; justify-content: center; flex: none; }

  /* Footer */
  .site-footer { position: absolute; left: 0; top: 903px; width: 1087px; height: 297px; background: var(--footer-bg); border-top: 1px solid var(--line); }
  .footer-col { position: absolute; top: 28px; }
  .footer-col p { font-size: 12px; color: #444; line-height: 18.5px; }
  .footer-col .section-heading { margin-bottom: 8px; font-size: 20px; }
  .call-now { position: absolute; left: 65px; top: 142px; }
  .call-now .section-heading { font-size: 19px; }
  .call-now .number { display: flex; align-items: center; gap: 7px; font-family: "Teko", sans-serif; font-weight: 500; font-size: 28px; color: var(--green); line-height: 1; margin-top: 8px; }
  .footer-rule { position: absolute; left: 67px; top: 252px; width: 973px; height: 1px; background: var(--line); }
  .copyright { position: absolute; left: 67px; top: 266px; font-size: 12px; color: #444; }
</style>
</head>
<body>

<header class="site-header">
  <div class="brand">
    <span class="brand-mark"></span>
    <span class="brand-name">Marri Ecoservices</span>
  </div>
  <div class="call-top">
    <div class="label">Call Us</div>
    <div class="number">0400 628 173</div>
  </div>
  <div class="search">
    <span>Search</span>
    <svg width="14" height="14" viewBox="0 0 14 14" aria-hidden="true"><circle cx="6" cy="6" r="4.5" fill="none" stroke="#999" stroke-width="1.6"/><line x1="9.3" y1="9.3" x2="13" y2="13" stroke="#999" stroke-width="1.8"/></svg>
  </div>
</header>

<nav class="main-nav">
  <ul>
    <li>Home</li>
    <li>Environmental Planning and Management</li>
    <li>Revegetation and Bush Regeneration</li>
    <li>About Us</li>
    <li class="is-active">Contact</li>
  </ul>
</nav>

<div class="banner" role="img" aria-label="Panoramic photograph of a rocky coastline with headland cliffs, beach and blue sea under a cloudy sky"></div>

<h1 class="page-title">Contact</h1>

<form class="contact-form">
  <label class="field-label" style="left:24px;top:25px">First Name<span class="req">*</span></label>
  <label class="field-label" style="left:324px;top:25px">Last Name<span class="req">*</span></label>
  <div class="field" style="left:24px;top:48px;width:276px;height:28px"></div>
  <div class="field" style="left:324px;top:48px;width:276px;height:28px"></div>

  <label class="field-label" style="left:24px;top:89px">Email</label>
  <label class="field-label" style="left:324px;top:89px">Phone Number<span class="req">*</span></label>
  <div class="field" style="left:24px;top:112px;width:276px;height:28px"></div>
  <div class="field" style="left:324px;top:112px;width:276px;height:28px"></div>

  <label class="field-label" style="left:24px;top:157px">Message<span class="req">*</span></label>
  <div class="field" style="left:24px;top:180px;width:576px;height:178px"></div>

  <span class="require-note"><span class="req">*</span> Require field</span>
  <div class="submit">Submit</div>
</form>

<aside class="contact-info">
  <h2 class="section-heading">Contact Info</h2>
  <div class="info-item" style="top:34px">
    <span class="info-icon"><svg width="12" height="14" viewBox="0 0 12 14" aria-hidden="true"><path d="M6 0C2.7 0 0.5 2.4 0.5 5.2 0.5 8.8 6 14 6 14s5.5-5.2 5.5-8.8C11.5 2.4 9.3 0 6 0z" fill="#8a8a8a"/><circle cx="6" cy="5.2" r="2" fill="#e3e3e3"/></svg></span>
    <span>&nbsp;12 Tuart Ave Wandoo<br>Creek SA 5999</span>
  </div>
  <div class="info-item" style="top:90px">
    <span class="info-icon"><svg width="14" height="14" viewBox="0 0 14 14" aria-hidden="true"><path d="M3 1l2.2 2.8-1.3 1.6c.8 1.8 2 3 3.8 3.8l1.6-1.3L12 10l-1.4 2.4C6 12.3 1.7 8 1.6 3.4z" fill="#8a8a8a"/></svg></span>
    <span>Phone :<br>0400 628 173</span>
  </div>
  <div class="info-item" style="top:149px">
    <span class="info-icon"><svg width="14" height="12" viewBox="0 0 14 12" aria-hidden="true"><path d="M1 5l6-4 6 4v6H1z" fill="#8a8a8a"/><path d="M1 5l6 4 6-4" fill="none" stroke="#e3e3e3" stroke-width="1.2"/></svg></span>
    <span>Email :<br>info@marriecoservices.com.au</span>
  </div>
</aside>

<footer class="site-footer">
  <div class="footer-col" style="left:67px">
    <h2 class="section-heading">About</h2>
    <p>Environmental Planning and Management<br>Revegetation and Bush Regeneration<br>Contacts</p>
  </div>
  <div class="footer-col" style="left:341px">
    <h2 class="section-heading">Website</h2>
    <p>www.marriecoservices.com.au</p>
  </div>
  <div class="call-now">
    <h2 class="section-heading">Call Us Now:</h2>
    <div class="number">
      <svg width="20" height="20" viewBox="0 0 14 14" aria-hidden="true"><path d="M3 1l2.2 2.8-1.3 1.6c.8 1.8 2 3 3.8 3.8l1.6-1.3L12 10l-1.4 2.4C6 12.3 1.7 8 1.6 3.4z" fill="#555"/></svg>
      <span>0400 628 173</span>
    </div>
  </div>
  <div class="footer-rule"></div>
  <p class="copyright">© 2015 Marri Ecoservices. All Rights Reserved.</p>
</footer>

</body>
</html>
```